Structural Engineering Business Card

Brookvane Drafting does residential house plans for clients in Central Florida. Would like simple but elegant business card that is appropriate for a house plan engineering company. Prefer black business card with black/white them but open to other shades of blue. I uploaded a sample card that I came across that looked good but please come up with your own creative designs.

Contact Information for Business Card

Name, Title, Phone, Email, Address, website

```html
<!DOCTYPE html>
<html lang="en">
<head>
<meta charset="utf-8">
<title>Brookvane Drafting — Business Card</title>
<link rel="stylesheet" href="https://fonts.googleapis.com/css2?family=Roboto:wght@400;700;900&display=swap">
<style>
  :root {
    --page-bg: #111113;
    --card-bg: #1d1d1f;
    --ink: #ffffff;
    --rule: #d9d9d9;
  }
  * { margin: 0; padding: 0; box-sizing: border-box; }
  html, body {
    width: 1200px;
    height: 900px;
    overflow: hidden;
    background: var(--page-bg);
    font-family: "Roboto", Arial, sans-serif;
    color: var(--ink);
  }
  .canvas {
    width: 1200px;
    height: 900px;
    display: flex;
    align-items: center;
    justify-content: center;
  }
  .card {
    position: relative;
    width: 980px;
    height: 560px;
    background: var(--card-bg);
    box-shadow: 0 20px 50px rgba(0,0,0,0.6);
    display: flex;
    align-items: center;
  }
  .brand {
    width: 510px;
    padding-left: 80px;
    margin-top: -60px;
  }
  .brand-name {
    font-weight: 900;
    font-size: 58px;
    line-height: 1.02;
    text-transform: uppercase;
    letter-spacing: 1px;
  }
  .divider {
    width: 1px;
    height: 320px;
    background: var(--rule);
    margin-top: 60px;
  }
  .details {
    padding-left: 44px;
    margin-top: 40px;
  }
  .person-name {
    font-weight: 700;
    font-size: 30px;
    text-transform: uppercase;
    letter-spacing: 0.5px;
    line-height: 1.1;
  }
  .person-title {
    font-size: 22px;
    margin-bottom: 18px;
  }
  .address {
    font-size: 21px;
    line-height: 1.3;
    margin-bottom: 22px;
    font-style: normal;
  }
  .contact-list { list-style: none; }
  .contact-item {
    display: flex;
    align-items: center;
    gap: 10px;
    font-size: 21px;
    line-height: 1.45;
  }
  .contact-icon {
    width: 18px;
    height: 18px;
    flex: none;
    fill: var(--ink);
  }
</style>
</head>
<body>
<main class="canvas">
  <section class="card">
    <div class="brand">
      <p class="brand-name">Brookvane<br>Drafting</p>
    </div>
    <div class="divider"></div>
    <div class="details">
      <h1 class="person-name">Marcus Hale</h1>
      <p class="person-title">Founder/CEO</p>
      <address class="address">2270 Harbor Lane Suite 140<br>Lakewood, FL 32801</address>
      <ul class="contact-list">
        <li class="contact-item">
          <svg class="contact-icon" viewBox="0 0 24 24" aria-hidden="true"><path d="M6.6 10.8a15.1 15.1 0 0 0 6.6 6.6l2.2-2.2a1 1 0 0 1 1-.25 11.4 11.4 0 0 0 3.6.57 1 1 0 0 1 1 1V20a1 1 0 0 1-1 1A17 17 0 0 1 3 4a1 1 0 0 1 1-1h3.5a1 1 0 0 1 1 1c0 1.25.2 2.45.57 3.57a1 1 0 0 1-.25 1z"/></svg>
          <span>555.018.2047</span>
        </li>
        <li class="contact-item">
          <svg class="contact-icon" viewBox="0 0 24 24" aria-hidden="true"><path d="M2 5h20v14H2z M3.5 6.5 12 13l8.5-6.5" fill="none" stroke="#fff" stroke-width="2"/></svg>
          <span>info@brookvanedrafting.com</span>
        </li>
        <li class="contact-item">
          <svg class="contact-icon" viewBox="0 0 24 24" aria-hidden="true"><g fill="none" stroke="#fff" stroke-width="1.8"><circle cx="12" cy="12" r="9.5"/><ellipse cx="12" cy="12" rx="4" ry="9.5"/><path d="M2.5 12h19"/></g></svg>
          <span>www.brookvanedrafting.com</span>
        </li>
      </ul>
    </div>
  </section>
</main>
</body>
</html>
```